Redesign of business card for Cedar Ridge Mechanical

We are looking for a new design for our business cards for Cedar Ridge Mechanical. We are a plumbing & HVAC construction company, operating on the West Coast of Canada and USA. Logo attached.
Industry/Entity Type
Construction - Plumbing & HVAC
Contact Information for Business Card
Name, address, phone numbers, email, website address
Look and feel
Each slider illustrates characteristics of the customer's brand and the style your logo design should communicate.

```html
<!DOCTYPE html>
<html lang="en">
<head>
<meta charset="utf-8">
<title>Cedar Ridge Mechanical – Business Card</title>
<link rel="stylesheet" href="https://fonts.googleapis.com/css2?family=Poppins:wght@300;400;600&display=swap">
<style>
  :root {
    --backdrop: #232323;
    --card-dark: #212124;
    --card-light: #e4e5e4;
    --ink-light: #ffffff;
    --ink-soft: #d9d9d9;
    --rule: #8a8a8a;
    --mark-faint: #f3f3f3;
  }
  * { margin: 0; padding: 0; box-sizing: border-box; }
  html, body { width: 1200px; height: 780px; overflow: hidden; }
  body {
    background: var(--backdrop);
    font-family: "Poppins", sans-serif;
    display: flex;
    align-items: center;
    justify-content: center;
    gap: 40px;
  }
  .card {
    position: relative;
    width: 540px;
    height: 309px;
    border-radius: 2px;
    overflow: hidden;
  }
  .card--front { background: var(--card-dark); color: var(--ink-light); }
  .card--back {
    background: var(--card-light);
    display: flex;
    align-items: center;
    justify-content: center;
  }

  .brand {
    position: absolute;
    left: 34px;
    top: 92px;
    width: 210px;
    display: flex;
    align-items: center;
    gap: 12px;
  }
  .brand__square {
    flex: none;
    width: 34px;
    height: 34px;
    border: 4px solid var(--ink-light);
  }
  .brand__name {
    font-weight: 600;
    font-size: 17px;
    line-height: 1.2;
    letter-spacing: 0.02em;
    text-transform: uppercase;
    color: var(--ink-light);
  }

  .divider {
    position: absolute;
    left: 270px;
    top: 58px;
    width: 1px;
    height: 150px;
    background: linear-gradient(to bottom, transparent, var(--rule) 30%, var(--rule) 70%, transparent);
  }

  .person {
    position: absolute;
    left: 300px;
    top: 44px;
  }
  .person__name { font-size: 25px; line-height: 1.1; font-weight: 300; }
  .person__name strong { font-weight: 600; }
  .person__title { font-size: 12px; font-weight: 300; color: var(--ink-soft); margin-top: 2px; }

  .contacts {
    position: absolute;
    left: 300px;
    top: 128px;
    list-style: none;
    font-size: 12px;
    font-weight: 300;
    line-height: 22px;
  }
  .contacts li { display: flex; align-items: center; gap: 9px; }
  .contacts svg { width: 12px; height: 12px; flex: none; }

  .address {
    position: absolute;
    left: 0;
    right: 0;
    bottom: 34px;
    text-align: center;
    font-size: 13px;
    font-weight: 300;
    letter-spacing: 0.01em;
  }

  .back-brand {
    display: flex;
    align-items: center;
    gap: 18px;
  }
  .back-brand__square {
    width: 54px;
    height: 54px;
    border: 5px solid var(--mark-faint);
  }
  .back-brand__name {
    font-weight: 600;
    font-size: 28px;
    line-height: 1.15;
    text-transform: uppercase;
    letter-spacing: 0.02em;
    color: var(--mark-faint);
  }
</style>
</head>
<body>

  <section class="card card--front" aria-label="Business card front">
    <div class="brand">
      <span class="brand__square" aria-hidden="true"></span>
      <span class="brand__name">Cedar Ridge<br>Mechanical</span>
    </div>

    <div class="divider" aria-hidden="true"></div>

    <div class="person">
      <p class="person__name"><strong>Marta</strong> Kolar</p>
      <p class="person__title">Founder &amp; CEO</p>
    </div>

    <ul class="contacts">
      <li>
        <svg viewBox="0 0 24 24" aria-hidden="true"><path fill="#fff" d="M6.6 10.8a15 15 0 0 0 6.6 6.6l2.2-2.2a1 1 0 0 1 1-.25 11.4 11.4 0 0 0 3.6.57 1 1 0 0 1 1 1V20a1 1 0 0 1-1 1A17 17 0 0 1 3 4a1 1 0 0 1 1-1h3.5a1 1 0 0 1 1 1c0 1.25.2 2.45.57 3.6a1 1 0 0 1-.25 1z"/></svg>
        (604) 555-0148
      </li>
      <li>
        <svg viewBox="0 0 24 24" aria-hidden="true"><rect x="2" y="5" width="20" height="14" rx="2" fill="#fff"/><path d="M3 6l9 7 9-7" stroke="#212124" stroke-width="2" fill="none"/></svg>
        info@cedarridgemech.com
      </li>
      <li>
        <svg viewBox="0 0 24 24" aria-hidden="true"><circle cx="12" cy="12" r="9.5" fill="none" stroke="#fff" stroke-width="2"/><ellipse cx="12" cy="12" rx="4" ry="9.5" fill="none" stroke="#fff" stroke-width="1.6"/><path d="M2.5 12h19" stroke="#fff" stroke-width="1.6"/></svg>
        www.cedarridgemech.com
      </li>
    </ul>

    <p class="address">1840 Harbor View Rd. Suite 300 Portland, OR 97209</p>
  </section>

  <section class="card card--back" aria-label="Business card back">
    <div class="back-brand">
      <span class="back-brand__square" aria-hidden="true"></span>
      <span class="back-brand__name">Cedar Ridge<br>Mechanical</span>
    </div>
  </section>

</body>
</html>
```